Machining Business Order Thank You Insert

I am looking for a business style card to include with orders that I ship. The card needs to thank the recipient for their order, and encourage them to leave a review. The card should include my business name and contact information and have an area to hand write a message.

I mainly sale on Craftlane and my own website. We are a machining an manufacturing business that are in the sale of mostly metal machined and 3d printed plastic products.

The front of the card should include the following:
Logo: (attached)
Snapgram: https://www.snapgram.example/kelvomill/
Friendsbook: https://www.friendsbook.example/KelvoMill
Website: https://www.kelvomill.example/

The back of the card needs an area to write a message

Industry/Entity Type

3D Printing, Machining, Craftlane

Contact Information for Business Card

Black or white front, white back to write a personal message

Font styles to use
Sans Serif

Colors

Designer to choose colors to be used in the design.

Requirements
Must have
• Encourage a review, social media info

```html
<!DOCTYPE html>
<html lang="en">
<head>
<meta charset="utf-8">
<title>KelvoMill Order Thank You Card</title>
<link rel="stylesheet" href="https://fonts.googleapis.com/css2?family=Montserrat:wght@400;500;600&family=Roboto:wght@400;500&display=swap">
<style>
  :root {
    --stage: #1b1b1b;
    --card-black: #262626;
    --card-black-edge: #2f2f2f;
    --silver: #d9d9d9;
    --silver-soft: #bdbdbd;
    --silver-dim: #8c8c8c;
    --metal-light: #f2f2f2;
    --metal-mid: #b8b8b8;
    --metal-dark: #7a7a7a;
    --paper: #ffffff;
    --ink: #2a2a2a;
    --ink-soft: #6b6b6b;
    --rule: #c9c9c9;
  }
  * { box-sizing: border-box; margin: 0; padding: 0; }
  html, body { width: 1200px; height: 900px; overflow: hidden; }
  body {
    background: radial-gradient(ellipse at 50% 40%, #2a2a2a 0%, var(--stage) 70%);
    position: relative;
    font-family: "Roboto", Arial, sans-serif;
  }
  .card {
    position: absolute;
    left: 280px;
    width: 640px;
    height: 366px;
    border-radius: 3px;
    box-shadow: 0 14px 30px rgba(0,0,0,0.55);
  }
  .card-back {
    top: 60px;
    padding: 18px;
    background: linear-gradient(115deg, var(--metal-dark) 0%, var(--metal-mid) 22%, var(--metal-light) 45%, var(--metal-mid) 65%, var(--metal-dark) 100%);
  }
  .message-panel {
    width: 100%;
    height: 100%;
    background: var(--paper);
    border-radius: 2px;
    padding: 26px 40px 24px;
    display: flex;
    flex-direction: column;
    color: var(--ink);
  }
  .thanks-title {
    font-family: "Montserrat", sans-serif;
    font-weight: 600;
    font-size: 24px;
    letter-spacing: 0.14em;
    text-align: center;
  }
  .review-prompt {
    font-family: "Montserrat", sans-serif;
    font-weight: 400;
    font-size: 13px;
    letter-spacing: 0.04em;
    color: var(--ink-soft);
    text-align: center;
    margin-top: 8px;
  }
  .write-lines {
    flex: 1;
    margin-top: 18px;
    display: flex;
    flex-direction: column;
    justify-content: space-evenly;
  }
  .write-line { height: 1px; background: var(--rule); }
  .card-front {
    top: 474px;
    background: linear-gradient(135deg, var(--card-black-edge) 0%, var(--card-black) 60%, #1f1f1f 100%);
    display: flex;
    align-items: center;
  }
  .brand {
    width: 270px;
    display: flex;
    flex-direction: column;
    align-items: center;
    gap: 26px;
  }
  .brand-square {
    width: 92px;
    height: 92px;
    border: 3px solid var(--silver-soft);
  }
  .brand-name {
    font-family: "Montserrat", sans-serif;
    font-weight: 500;
    font-size: 24px;
    letter-spacing: 0.32em;
    color: var(--silver);
  }
  .divider {
    width: 1px;
    height: 210px;
    background: var(--silver-dim);
  }
  .details {
    padding-left: 34px;
    color: var(--silver);
  }
  .person-name {
    font-family: "Montserrat", sans-serif;
    font-weight: 500;
    font-size: 30px;
    letter-spacing: 0.04em;
    line-height: 1;
    color: var(--silver-soft);
  }
  .person-title {
    font-family: "Montserrat", sans-serif;
    font-weight: 500;
    font-size: 15px;
    letter-spacing: 0.06em;
    color: var(--silver-soft);
    margin-top: 4px;
    margin-bottom: 14px;
  }
  .contact-list { list-style: none; }
  .contact-list li {
    display: flex;
    align-items: center;
    gap: 7px;
    font-size: 17px;
    line-height: 24px;
    color: var(--silver);
    white-space: nowrap;
  }
  .contact-list .gap-above { margin-top: 8px; }
  .contact-icon { width: 14px; height: 14px; flex: none; }
  .contact-marker {
    width: 13px; height: 13px; flex: none;
    border-radius: 3px;
    background: var(--silver-soft);
  }
</style>
</head>
<body>
  <section class="card card-back">
    <div class="message-panel">
      <h1 class="thanks-title">THANK YOU FOR YOUR ORDER</h1>
      <p class="review-prompt">Enjoying your piece? Please leave us a review on Craftlane or our website.</p>
      <div class="write-lines">
        <div class="write-line"></div>
        <div class="write-line"></div>
        <div class="write-line"></div>
        <div class="write-line"></div>
        <div class="write-line"></div>
      </div>
    </div>
  </section>

  <section class="card card-front">
    <div class="brand">
      <div class="brand-square"></div>
      <div class="brand-name">KELVOMILL</div>
    </div>
    <div class="divider"></div>
    <div class="details">
      <div class="person-name">ROWAN PELL</div>
      <div class="person-title">DIRECTOR</div>
      <ul class="contact-list">
        <li>
          <svg class="contact-icon" viewBox="0 0 14 14"><rect width="14" height="14" rx="3" fill="#bdbdbd"/><path d="M4 3.5l1.6-.3.9 2-1 .8a6 6 0 0 0 2.5 2.5l.8-1 2 .9-.3 1.6c-3.5.3-6.8-3-6.5-6.5z" fill="#262626"/></svg>
          401-555-0187
        </li>
        <li>
          <svg class="contact-icon" viewBox="0 0 14 14"><rect width="14" height="14" rx="3" fill="#bdbdbd"/><rect x="3" y="4.2" width="8" height="5.6" fill="none" stroke="#262626" stroke-width="1"/><path d="M3 4.2l4 3 4-3" fill="none" stroke="#262626" stroke-width="1"/></svg>
          info@kelvomill.example
        </li>
        <li class="gap-above"><span class="contact-marker"></span>www.snapgram.example/kelvomill</li>
        <li><span class="contact-marker"></span>www.friendsbook.example/KelvoMill</li>
        <li><span class="contact-marker"></span>www.kelvomill.example</li>
      </ul>
    </div>
  </section>
</body>
</html>
```